International Trade Consulting Firm Seeks Quality Newsletter Design

Our company provides consulting services to Pinnacle 300 type companies. We compete with the largest consulting companies in the world. However, we have the highest level of expertise in the industry and need to look the most professional and high end. We have very relevant and important information to provide our customers about their compliance and projects. We will have the winning design coded to be an e-newsletter, so it needs to be one page. We want to keep our company colors and logo design in the newsletter, they are attached. We DO NOT want it to look like a mini-version of our website. We want a fresh look to this marketing piece. Newsletter will need to include title, possible sub-heading, space for a feature story, 2 other stories included, and space on either the left or right for short cuts, links or highlights of other articles. Contents/'In this issue' section, about us or branding area, section for relevant links, etc...
Pinnacle 300 companies, High-level management
Marketing

```html
<!DOCTYPE html>
<html lang="en">
<head>
<meta charset="utf-8">
<title>Happy mail! — Harborline Trade Corporation Newsletter Vol. 1</title>
<link rel="stylesheet" href="https://fonts.googleapis.com/css2?family=Arimo:wght@400;700&family=Nunito:wght@800;900&family=Rammetto+One&display=swap">
<style>
  :root {
    --black: #060806;
    --band-green: #3f8a35;
    --band-green-dark: #2c6a26;
    --hero-green: #2c5a24;
    --hero-green-right: #23491d;
    --deep-green: #13240f;
    --deep-green-left: #0f1e0c;
    --cream: #e2d6a4;
    --cream-soft: #d8ceaa;
    --text-light: #e9ecdf;
    --btn-green: #11883c;
    --btn-green-dark: #0a6a2c;
    --link: #d9dfc8;
  }
  * { box-sizing: border-box; margin: 0; padding: 0; }
  html, body { width: 786px; height: 1200px; overflow: hidden; background: var(--black); }
  body { font-family: "Arimo", Arial, sans-serif; color: var(--text-light); }
  .newsletter { position: relative; width: 786px; height: 1200px; overflow: hidden; background: var(--deep-green); }
  .abs { position: absolute; }

  /* masthead */
  .masthead { left: 0; top: 0; width: 786px; height: 138px; background: var(--black); }
  .browser-note { right: 38px; top: 10px; font-size: 9.6px; color: #d9d9d9; }
  .browser-note a { color: #d9d9d9; }
  .brand { left: 32px; top: 24px; width: 219px; height: 96px; background: #0d0d0b; display: flex; align-items: center; justify-content: center; gap: 9px; }
  .brand-mark { width: 13px; height: 13px; background: var(--cream); flex: none; }
  .brand-name { font-family: "Arimo", Arial, sans-serif; font-weight: 700; font-size: 18px; color: var(--cream); letter-spacing: 0.5px; line-height: 1.1; }
  .title-happy { right: 37px; top: 52px; font-family: "Rammetto One", "Cooper Black", serif; font-size: 35px; color: var(--cream); line-height: 1; }

  .tagline-band { left: 0; top: 138px; width: 786px; height: 49px; background: linear-gradient(180deg, var(--band-green) 0%, var(--band-green-dark) 100%); }
  .tagline { left: 41px; top: 145px; font-family: "Nunito", Arial, sans-serif; font-weight: 900; font-size: 28px; color: var(--cream); }
  .volume { right: 38px; top: 157px; font-weight: 700; font-size: 16px; color: #fff; }

  /* hero */
  .hero { left: 0; top: 187px; width: 786px; height: 284px; background: var(--hero-green); }
  .hero-right { left: 423px; top: 187px; width: 363px; height: 284px; background: linear-gradient(135deg, var(--hero-green) 0%, var(--hero-green-right) 100%); }
  .hero-photo { left: 38px; top: 199px; width: 377px; height: 251px; background: linear-gradient(160deg, #d7e4ec 0%, #9aa9b3 45%, #3b3f47 100%); }
  .hero-heading { right: 39px; top: 205px; font-family: "Nunito", Arial, sans-serif; font-weight: 900; font-size: 23.5px; color: var(--cream); }
  .hero-copy { left: 458px; top: 254px; width: 289px; font-size: 11px; line-height: 13.3px; text-align: justify; color: var(--text-light); }

  .btn { display: flex; align-items: center; justify-content: center; background: linear-gradient(180deg, var(--btn-green) 0%, var(--btn-green-dark) 100%); color: #fff; font-weight: 700; border-radius: 3px; text-decoration: none; }
  .btn-hero { left: 654px; top: 422px; width: 94px; height: 23px; font-size: 12.5px; }
  .btn-small { width: 64px; height: 16px; font-size: 8.5px; }

  /* section band */
  .section-band { left: 0; top: 471px; width: 786px; height: 44px; background: var(--black); }
  .section-title { top: 484px; font-family: "Nunito", Arial, sans-serif; font-weight: 800; font-size: 19px; color: var(--cream-soft); }
  .section-title.left { left: 38px; }
  .section-title.right { right: 39px; }

  .left-col { left: 0; top: 515px; width: 419px; height: 645px; background: var(--deep-green-left); }

  /* feature */
  .feature-art { left: 38px; top: 515px; width: 376px; height: 328px; background: linear-gradient(150deg, #6b6470 0%, #cfc4be 45%, #b9825c 75%, #eae3da 100%); }
  .feature-heading { left: 37px; top: 845px; font-family: "Nunito", Arial, sans-serif; font-weight: 900; font-size: 23px; color: var(--cream-soft); }
  .feature-copy { left: 37px; top: 879px; width: 376px; font-size: 9.6px; line-height: 12px; text-align: justify; }
  .btn-feature { left: 351px; top: 933px; }

  /* issue list */
  .issue-list { left: 454px; top: 514px; list-style: none; }
  .issue-list li { display: flex; align-items: center; height: 24px; font-size: 9.8px; }
  .issue-list svg { margin-right: 14px; }
  .issue-list a { color: var(--link); }

  .story-label { right: 39px; font-family: "Nunito", Arial, sans-serif; font-weight: 800; font-size: 14px; color: var(--cream-soft); }
  .story-title { right: 38px; text-align: right; color: var(--cream-soft); text-decoration: underline; }
  .story-copy { left: 594px; width: 154px; font-size: 7px; line-height: 9px; text-align: justify; color: #d2d6c8; }

  .story1-img { left: 452px; top: 698px; width: 123px; height: 83px; background: linear-gradient(180deg, #8fb3d6 0%, #3e6b9a 55%, #12233b 100%); }
  .story1-title { top: 696px; font-size: 12.5px; line-height: 15px; }
  .story1-copy { top: 733px; }

  .story2-img { left: 454px; top: 828px; width: 115px; height: 83px; background: radial-gradient(circle at 45% 45%, #8593a6 0%, #3b4656 55%, #141b25 100%); }
  .story2-title { top: 828px; font-size: 10.5px; line-height: 12.5px; }
  .story2-copy { left: 596px; top: 864px; width: 152px; }
  .btn-story { left: 684px; top: 931px; }

  /* leader */
  .block-heading { top: 966px; font-family: "Nunito", Arial, sans-serif; font-weight: 900; font-size: 19px; color: var(--cream); text-decoration: underline; }
  .leader-heading { left: 45px; }
  .news-heading { right: 38px; }
  .leader-photo { left: 43px; top: 1010px; width: 80px; height: 87px; border: 1px solid #9b9b93; background: linear-gradient(180deg, #c9ccc8 0%, #a8aca9 50%, #2a2e36 100%); }
  .leader-bio { left: 147px; top: 1006px; width: 273px; font-size: 9.6px; line-height: 11.8px; text-align: justify; }
  .btn-leader { left: 356px; top: 1110px; }

  .news-list { left: 459px; top: 1004px; width: 289px; list-style: none; }
  .news-list li { font-size: 9.6px; line-height: 12px; text-align: justify; }
  .news-list li + li { margin-top: 9px; padding-top: 9px; border-top: 1px dotted #b9bcae; }
  .news-list li:nth-child(1) { padding-bottom: 4px; }
  .news-list li:nth-child(2) { padding-bottom: 4px; }

  .footer { left: 0; top: 1160px; width: 786px; height: 40px; background: var(--black); display: flex; align-items: center; justify-content: center; font-size: 12.5px; color: #ececec; padding-right: 4px; }
</style>
</head>
<body>
<div class="newsletter">

  <header class="masthead abs"></header>
  <p class="browser-note abs">Is this email not displaying correctly? View it in your <a href="#">browser</a></p>
  <div class="brand abs"><span class="brand-mark"></span><span class="brand-name">Harborline Trade</span></div>
  <h1 class="title-happy abs">Happy mail!</h1>

  <div class="tagline-band abs"></div>
  <h2 class="tagline abs">We have a good news for you!</h2>
  <span class="volume abs">VOL. 1</span>

  <section class="hero abs"></section>
  <div class="hero-right abs"></div>
  <div class="hero-photo abs" role="img" aria-label="Business team meeting around a conference table with a presenter at a whiteboard"></div>
  <h3 class="hero-heading abs">Hey, good news !</h3>
  <p class="hero-copy abs">Lorem ipsum dolor sit amet, consectetuer adipiscing elit, sed diam nonummy nibh euismod tincidunt ut laoreet dolore magna aliquam erat volutpat. Ut wisi enim ad minim veniam, quis nostrud exerci tation ullamcorper suscipit lobortis nisl ut aliquip ex ea commodo consequat. Duis autem vel eum iriure dolor in hendrerit in vulputate velit esse molestie consequat, vel illum dolore eu feugiat nulla facilisis at vero eros et accumsan et iusto odio dignissim qui blandit praesent luptatum zzril delenit augue duis dolore te feugait nulla facilisi. Nam liber tempor cum soluta nobis eleifend option congue nihil imperdiet doming id</p>
  <a class="btn btn-hero abs" href="#">READ MORE</a>

  <div class="section-band abs"></div>
  <div class="left-col abs"></div>
  <h3 class="section-title left abs">Featured Story</h3>
  <h3 class="section-title right abs">In this Issue</h3>

  <div class="feature-art abs" role="img" aria-label="Illustration of a red and white arrow block hoisted by a crane hook and chains"></div>
  <h3 class="feature-heading abs">Save Money on processing fees</h3>
  <p class="feature-copy abs">Lorem ipsum dolor sit amet, consectetuer adipiscing elit, sed diam nonummy nibh euismod tincidunt ut laoreet dolore magna aliquam erat volutpat. Ut wisi enim ad minim veniam, quis nostrud exerci tation ullamcorper suscipit lobortis nisl ut aliquip ex</p>
  <a class="btn btn-small btn-feature abs" href="#">READ MORE</a>

  <ul class="issue-list abs">
    <li><svg width="9" height="9" viewBox="0 0 9 9"><path d="M1 1 L8 4.5 L1 8 Z" fill="none" stroke="#cfd3c3" stroke-width="1"/></svg><a href="#">Save Money on processing fees</a></li>
    <li><svg width="9" height="9" viewBox="0 0 9 9"><path d="M1 1 L8 4.5 L1 8 Z" fill="none" stroke="#cfd3c3" stroke-width="1"/></svg><a href="#">Advantages of running a business In a foreign Trade zone</a></li>
    <li><svg width="9" height="9" viewBox="0 0 9 9"><path d="M1 1 L8 4.5 L1 8 Z" fill="none" stroke="#cfd3c3" stroke-width="1"/></svg><a href="#">Unlock your International Business Possibilities</a></li>
    <li><svg width="9" height="9" viewBox="0 0 9 9"><path d="M1 1 L8 4.5 L1 8 Z" fill="none" stroke="#cfd3c3" stroke-width="1"/></svg><a href="#">Foreign Trade zone Project Engineering</a></li>
    <li><svg width="9" height="9" viewBox="0 0 9 9"><path d="M1 1 L8 4.5 L1 8 Z" fill="none" stroke="#cfd3c3" stroke-width="1"/></svg><a href="#">Activations with U.S Customs &amp; Border Protection</a></li>
  </ul>

  <h4 class="story-label abs" style="top:662px">Story 1</h4>
  <div class="story1-img abs" role="img" aria-label="Two business people shaking hands in front of a tall office window"></div>
  <a class="story-title story1-title abs" href="#">Unlock your International<br>Business Possibilities</a>
  <p class="story-copy story1-copy abs">Lorem ipsum dolor sit amet, consectetuer adipiscing elit, sed diam nonummy nibh euismod tincidunt ut laoreet dolore magna aliquam erat volutpat. Ut wisi enim ad minim veniam, quis nostrud exerci tation ullamcorper</p>

  <h4 class="story-label abs" style="top:799px">Story 2</h4>
  <div class="story2-img abs" role="img" aria-label="Glowing global network of connected points on a dark background"></div>
  <a class="story-title story2-title abs" href="#">Activations with U.S Customs &amp;<br>Border Protection</a>
  <p class="story-copy story2-copy abs">Lorem ipsum dolor sit amet, consectetuer adipiscing elit, sed diam nonummy nibh euismod tincidunt ut laoreet dolore magna aliquam erat volutpat. Ut wisi enim ad minim veniam, quis nostrud exerci tation ullamcorper</p>
  <a class="btn btn-small btn-story abs" href="#">READ MORE</a>

  <h3 class="block-heading leader-heading abs">LEADER SPEAKS</h3>
  <div class="leader-photo abs" role="img" aria-label="Portrait of the company founder and president"></div>
  <p class="leader-bio abs">Daniel Reese is a founder and President of the Harborline Corporation. Mr. Reese has been involved in the Foreign-Trade Zones Program since 1989 when he began operating and administering Foreign-Trade Zone No. 61 in Marlow, Tennessee. This Zone's success set the standard nationwide for Intermodal FTZ Operations, JIT manufacturing Operations and distribution operations. In 1994, along with Mark Ellis, he formed the Harborline Trade Corporation.</p>
  <a class="btn btn-small btn-leader abs" href="#">READ MORE</a>

  <h3 class="block-heading news-heading abs">IN THE NEWS</h3>
  <ul class="news-list abs">
    <li>Access to Foreign-Trade Zones: Faster and Easier, Thanks to Recent Federal Regulations</li>
    <li>U.S. Foreign-Trade Zones Program Use Grows Among U.S. Based Manufacturing Operations</li>
    <li>Wexford Lane LLC Taps into Foreign-Trade Zone Value for Supply Chain, Partners with Harborline Trade Corporation (Harborline Corp)</li>
  </ul>

  <footer class="footer abs">Copyright 2014 Harborline Trade Corporation</footer>
</div>
</body>
</html>
```